Book cover for book about Climate Change

Looking for a clean, bold, and attractive cover for a mass-market paperback (5.5"x 8.5") about solving the climate change problem. Title is either "A Harbor Made of Glass” or A Harbor Made of Glass” (your choice), subtitle is "A practical field guide to mending the weather — so that the young ones after us inherit steady seasons and open skies," author is Lorne Whitcombe. Thinking that it *might* feature an image of Earth (or a portion thereof) and its very thin layer of atmosphere -- but STRONGLY encourage other ideas too!

Requirements
Nice to have
• Keep it positive — NOT scary doom-and-gloom

```html
<!DOCTYPE html>
<html lang="en">
<head>
<meta charset="utf-8">
<title>A Harbor Made of Glass — Lorne Whitcombe</title>
<link rel="stylesheet" href="https://fonts.googleapis.com/css2?family=Barlow+Semi+Condensed:wght@700&family=Barlow:wght@700&family=Inter:wght@700&display=swap">
<style>
  :root {
    --backdrop: #efd6b3;
    --cover-plum: #3c0f36;
    --accent-gold: #f2b918;
    --title-white: #ffffff;
    --globe-deep: #0b1733;
    --globe-lit: #3f6fae;
  }
  html, body {
    margin: 0;
    padding: 0;
    width: 1200px;
    height: 1200px;
    overflow: hidden;
    background: var(--backdrop);
  }
  .canvas {
    position: relative;
    width: 1200px;
    height: 1200px;
  }
  .book-cover {
    position: absolute;
    left: 342px;
    top: 90px;
    width: 588px;
    height: 907px;
    background: var(--cover-plum);
    text-align: center;
  }
  .author-name {
    position: absolute;
    top: 50px;
    left: 0;
    right: 0;
    margin: 0;
    font-family: "Barlow", sans-serif;
    font-weight: 700;
    font-size: 46px;
    letter-spacing: 0.13em;
    color: var(--accent-gold);
    line-height: 1;
  }
  .book-title {
    position: absolute;
    top: 150px;
    left: 0;
    right: 0;
    margin: 0;
    font-family: "Inter", sans-serif;
    font-weight: 700;
    font-size: 122px;
    letter-spacing: -5px;
    line-height: 103px;
    color: var(--title-white);
  }
  .title-line { display: block; }
  .title-line--accent { color: var(--accent-gold); }
  .globe-letter {
    display: inline-block;
    width: 90px;
    height: 90px;
    margin-right: 2px;
    border-radius: 50%;
    vertical-align: -1px;
    background: radial-gradient(circle at 72% 40%, var(--globe-lit) 0%, #1d3466 38%, var(--globe-deep) 72%, var(--cover-plum) 100%);
  }
  .subtitle {
    position: absolute;
    top: 722px;
    left: 0;
    right: 0;
    margin: 0;
    font-family: "Barlow Semi Condensed", sans-serif;
    font-weight: 700;
    font-size: 23px;
    line-height: 33px;
    color: var(--title-white);
    text-transform: uppercase;
  }
  .subtitle-highlight { color: var(--accent-gold); }
</style>
</head>
<body>
  <main class="canvas">
    <section class="book-cover">
      <p class="author-name">LORNE WHITCOMBE</p>
      <h1 class="book-title">
        <span class="title-line">A</span>
        <span class="title-line">HARBOR</span>
        <span class="title-line">MADE</span>
        <span class="title-line"><span class="globe-letter" role="img" aria-label="Photograph of planet Earth from space, standing in for the letter O"></span>F</span>
        <span class="title-line title-line--accent">GLASS</span>
      </h1>
      <p class="subtitle">
        A practical <span class="subtitle-highlight">field guide</span> to <span class="subtitle-highlight">mending</span><br>
        the weather — so that the young ones<br>
        after us inherit steady seasons<br>
        and open skies.
      </p>
    </section>
  </main>
</body>
</html>
```